Venture Capital Firm Needs Website Redesign

We need a bold revamp of our website (https://halverine.vc/)
which at the moment looks washed out. We want a crisp, fresh and unique look. Feel free to keep as much or as little content in the site. The only thing we need to keep is a team section. The site should convey a clear distinction between our 3 product lines: Venture Capital, Private Credit, and Crypto. Two versions of our logo are attached and they should not change. For design inspirations, we like http://www.9plm.com/ for a more simple site and for a more built out site we like http://bluetorch.com/

Updates
Industry/Entity Type
Investment
Coding
Coded - Design and coding required
Number of Pages Required
1 page
Font styles to use
Colors
Designer to choose colors to be used in the design.
Requirements
Must have
- - Clear distinction between our 3 product lines: Venture Capital, Private Credit
- - Team section

Nice to have
- Some really creative aspect like http://www.9plm.com/ has with the distinction between first, second, and third kind

```html
<!DOCTYPE html>
<html lang="en">
<head>
<meta charset="utf-8">
<title>Halverine — Venture Capital, Private Credit, Crypto</title>
<link href="https://fonts.googleapis.com/css2?family=Open+Sans:wght@400;600;700&family=Roboto:wght@300;400;500;700&display=swap" rel="stylesheet">
<style>
:root{
  --olive:#8c9c2c;
  --olive-dark:#7a8a22;
  --olive-soft:#d6dcae;
  --ink:#333333;
  --text:#444444;
  --muted:#666666;
  --hero-bg:#f6f6f6;
  --band-bg:#f7f7f7;
  --ring:#d9d9d4;
  --disc:#ececec;
  --card-dark:#353535;
  --footer:#333333;
  --white:#ffffff;
}
*{box-sizing:border-box;margin:0;padding:0}
html,body{width:1200px;height:3066px;overflow:hidden}
body{position:relative;background:var(--white);font-family:"Open Sans",sans-serif;color:var(--text)}
.abs{position:absolute}
.btn{position:absolute;background:var(--olive);color:var(--white);border-radius:20px;font:600 12px "Open Sans",sans-serif;display:flex;align-items:center;justify-content:center;height:40px;width:162px}
/* hero */
.hero{position:absolute;left:0;top:0;width:1200px;height:760px;background:var(--hero-bg)}
.brand{position:absolute;left:119px;top:62px;font:300 44px "Roboto",sans-serif;color:var(--ink);letter-spacing:1px}
.menu{position:absolute;left:1044px;top:75px;width:34px}
.menu span{display:block;height:4px;background:var(--ink);margin-bottom:6px;border-radius:2px}
.hero-title{position:absolute;left:0;width:1200px;top:290px;text-align:center;font:700 37px/45px "Roboto",sans-serif;color:var(--ink)}
.hero-sub{position:absolute;left:0;width:1200px;top:381px;text-align:center;font:600 21px/29px "Open Sans",sans-serif;color:var(--ink)}
.dots{position:absolute;top:806px;left:572px;display:flex;gap:4px}
.dots i{width:10px;height:10px;border-radius:50%;border:1.5px solid #555;display:block}
.dots i.on{background:var(--olive);border-color:var(--olive)}
/* services */
.service{position:absolute;top:900px;width:420px;text-align:center}
.service-art{position:absolute;border-radius:10px;background:linear-gradient(135deg,var(--olive-soft),#e4e4e4)}
.service h2{margin-top:150px;font:500 31px "Roboto",sans-serif;color:var(--ink)}
.service h2 b{color:var(--olive);font-weight:500}
.service p{margin:10px auto 0;width:370px;font:400 13.5px/18px "Open Sans",sans-serif;color:var(--text)}
/* crypto */
.crypto{position:absolute;left:0;top:1331px;width:1200px;height:574px;background:var(--band-bg)}
.crypto h2{position:absolute;left:119px;top:152px;font:500 29px "Roboto",sans-serif;color:var(--ink)}
.crypto p{position:absolute;left:119px;top:210px;width:490px;font:400 13.5px/17px "Open Sans",sans-serif;color:var(--text)}
.chart{position:absolute;left:630px;top:108px}
/* team */
.team-title{position:absolute;left:0;width:1200px;top:1965px;text-align:center;font:500 31px "Roboto",sans-serif;color:var(--ink)}
.team-title b{color:var(--olive);font-weight:500}
.team-sub{position:absolute;left:0;width:1200px;top:2010px;text-align:center;font:400 14px "Open Sans",sans-serif;color:var(--text)}
.nav{position:absolute;top:1969px;width:28px;height:28px;border-radius:50%}
.card{position:absolute;top:2071px;width:221px;height:251px;background:var(--card-dark);border-radius:6px;text-align:center}
.card.active{background:var(--olive)}
.portrait{width:126px;height:126px;border-radius:50%;margin:18px auto 0;border:4px solid var(--white);background:radial-gradient(circle at 50% 40%,#bdbdbd,#7a7a7a)}
.card h3{margin-top:22px;font:700 19px "Roboto",sans-serif;color:var(--olive)}
.card.active h3{color:var(--white)}
.card .role{font:600 9px "Open Sans",sans-serif;color:var(--white);margin-top:2px}
.socials{display:flex;justify-content:center;gap:10px;margin-top:10px}
.socials i{width:24px;height:24px;border-radius:50%;background:var(--white);display:block}
/* newsletter */
.news-title{position:absolute;left:0;width:1200px;top:2480px;text-align:center;font:700 25px "Roboto",sans-serif;color:var(--ink)}
.news-title b{color:var(--olive)}
.news-sub{position:absolute;left:0;width:1200px;top:2518px;text-align:center;font:400 14px "Open Sans",sans-serif;color:var(--muted)}
.news-form{position:absolute;left:311px;top:2556px;width:556px;height:38px;border:1.5px solid #e2e2e2;border-radius:20px;overflow:hidden}
.news-form span{position:absolute;left:22px;top:10px;font:400 13px "Open Sans",sans-serif;color:#888}
.news-form .submit{position:absolute;right:0;top:0;width:126px;height:100%;background:var(--olive);color:var(--white);font:700 14px "Roboto",sans-serif;display:flex;align-items:center;justify-content:center}
/* footer */
.footer{position:absolute;left:0;top:2669px;width:1200px;height:348px;background:var(--footer);color:var(--white)}
.footer .brand-foot{position:absolute;left:119px;top:70px;font:300 40px "Roboto",sans-serif;color:var(--white);letter-spacing:1px}
.footer h4{position:absolute;top:85px;font:700 13px "Roboto",sans-serif;text-decoration:underline;text-underline-offset:6px}
.footer .about{position:absolute;left:119px;top:148px;width:260px;font:400 12.5px/16px "Open Sans",sans-serif}
.footer .more{position:absolute;left:119px;top:224px;font:400 14px "Open Sans",sans-serif}
.footer ul{position:absolute;left:437px;top:150px;list-style:none;font:400 13px/17px "Open Sans",sans-serif}
.footer ul li:before{content:"• ";}
.footer .contact{position:absolute;left:605px;top:148px;font:400 13.5px/26px "Open Sans",sans-serif}
.field{position:absolute;background:var(--white);border-radius:10px;font:400 10px "Open Sans",sans-serif;color:#999;padding:3px 12px}
.bottom{position:absolute;left:0;top:3017px;width:1200px;height:49px;background:var(--olive)}
.bottom p{position:absolute;left:119px;top:15px;font:400 14px "Open Sans",sans-serif;color:var(--white)}
.bottom .socials{position:absolute;left:902px;top:12px;margin:0;gap:12px}
</style>
</head>
<body>

<section class="hero">
  <div class="brand">HALVERINE</div>
  <div class="menu"><span></span><span></span><span></span></div>
  <svg class="abs" style="left:303px;top:100px" width="600" height="600" viewBox="0 0 600 600">
    <circle cx="300" cy="299" r="270" fill="none" stroke="var(--ring)" stroke-width="9"/>
    <rect x="292" y="20" width="16" height="14" fill="var(--hero-bg)"/>
    <rect x="292" y="562" width="16" height="14" fill="var(--hero-bg)"/>
    <circle cx="300" cy="299" r="255" fill="var(--disc)"/>
    <circle cx="28" cy="299" r="27" fill="var(--ring)"/>
    <circle cx="572" cy="299" r="27" fill="var(--ring)"/>
  </svg>
  <h1 class="hero-title">HALVERINE<br>OPERATES</h1>
  <p class="hero-sub">AT THE INTERSECTION OF TECHNOLOGY<br>AND NOVEL ASSET CLASSES.</p>
  <a class="btn" style="left:516px;top:451px">Read More</a>
</section>

<div class="dots"><i></i><i></i><i></i><i class="on"></i></div>

<section class="service" style="left:146px">
  <div class="service-art" style="left:140px;top:10px;width:150px;height:125px" role="img" aria-label="Illustration of a rocket launching between upward arrows, representing venture growth"></div>
  <h2><b>VENTURE</b> CAPITAL</h2>
  <p>We invest in early-stage startups led by founders who are passionate and knowledgeable about the markets they serve.</p>
  <a class="btn" style="left:130px;top:296px;width:161px">Read More</a>
</section>

<section class="service" style="left:644px">
  <div class="service-art" style="left:150px;top:18px;width:133px;height:110px" role="img" aria-label="Illustration of credit cards with a gear, representing private credit"></div>
  <h2><b>PRIVATE</b> CREDIT</h2>
  <p>Halverine Private Credit provides capital to lending businesses that are focused on using technology to establish new credit markets.</p>
  <a class="btn" style="left:132px;top:296px;width:161px">Read More</a>
</section>

<section class="crypto">
  <h2>CRYPTO</h2>
  <p>The Halverine Crypto Index tracks the top 15 cryptocurrencies weighted by market cap and rebalanced twice a month. We believe this is the simplest and most cost effective way to obtain cryptocurrency exposure. Our process has been designed by experts from financial services and cryptocurrency industries.</p>
  <a class="btn" style="left:122px;top:332px;width:161px">Read More</a>
  <svg class="chart" width="390" height="340" viewBox="0 0 390 340" font-family="Roboto, sans-serif">
    <text x="195" y="10" font-size="9" text-anchor="middle" fill="#333">HCI Cumulative Growth</text>
    <circle cx="92" cy="29" r="6" fill="var(--olive)"/><text x="102" y="32" font-size="8" fill="#666">HCI (1236.48%)</text>
    <circle cx="208" cy="29" r="6" fill="#111"/><text x="218" y="32" font-size="8" fill="#666">Benchmark (717.41%)</text>
    <g stroke="#e6e6e6" stroke-width="1">
      <line x1="38" y1="62" x2="378" y2="62"/><line x1="38" y1="92" x2="378" y2="92"/>
      <line x1="38" y1="122" x2="378" y2="122"/><line x1="38" y1="152" x2="378" y2="152"/>
      <line x1="38" y1="182" x2="378" y2="182"/><line x1="38" y1="212" x2="378" y2="212"/>
      <line x1="38" y1="242" x2="378" y2="242"/><line x1="38" y1="272" x2="378" y2="272"/>
    </g>
    <g font-size="9" fill="#666" text-anchor="end">
      <text x="32" y="65">3500</text><text x="32" y="95">3000</text><text x="32" y="125">2500</text>
      <text x="32" y="155">2000</text><text x="32" y="185">1500</text><text x="32" y="215">1000</text>
      <text x="32" y="245">500</text><text x="32" y="275">0</text>
    </g>
    <g font-size="9" fill="#666">
      <text transform="translate(48 305) rotate(-90)">Jan</text><text transform="translate(74 305) rotate(-90)">Feb</text>
      <text transform="translate(100 305) rotate(-90)">Mar</text><text transform="translate(126 305) rotate(-90)">Apr</text>
      <text transform="translate(152 305) rotate(-90)">May</text><text transform="translate(178 305) rotate(-90)">Jun</text>
      <text transform="translate(204 305) rotate(-90)">Jul</text><text transform="translate(230 305) rotate(-90)">Aug</text>
      <text transform="translate(256 305) rotate(-90)">Sep</text><text transform="translate(282 305) rotate(-90)">Oct</text>
      <text transform="translate(308 305) rotate(-90)">Nov</text><text transform="translate(334 305) rotate(-90)">Dec</text>
      <text transform="translate(360 305) rotate(-90)">Jan</text>
    </g>
    <polyline fill="none" stroke="var(--olive)" stroke-width="2.5" points="44,272 60,272 76,271 92,270 108,269 124,268 140,264 156,256 172,248 180,236 188,240 196,232 204,250 212,240 220,234 236,244 252,226 268,226 278,214 286,200 296,188 304,160 312,120 320,114 330,88 340,140 350,152 360,148 370,178 378,198"/>
    <polyline fill="none" stroke="#111" stroke-width="2.5" points="44,272 60,272 76,272 92,271 108,271 124,270 140,268 156,264 172,262 188,256 204,262 212,254 220,258 236,252 252,244 268,242 278,240 286,220 296,214 304,174 312,186 320,184 330,204 340,206 350,196 360,210 370,212 378,220"/>
  </svg>
</section>

<h2 class="team-title"><b>OUR</b> TEAM</h2>
<p class="team-sub">The very best helping the very best.</p>
<svg class="nav" style="left:1015px" viewBox="0 0 28 28"><circle cx="14" cy="14" r="14" fill="var(--ink)"/><path d="M16 8 L10 14 L16 20" stroke="#fff" stroke-width="3" fill="none"/></svg>
<svg class="nav" style="left:1050px" viewBox="0 0 28 28"><circle cx="14" cy="14" r="14" fill="var(--olive)"/><path d="M12 8 L18 14 L12 20" stroke="#fff" stroke-width="3" fill="none"/></svg>

<article class="card" style="left:119px">
  <div class="portrait" role="img" aria-label="Portrait of partner Omar Velasco"></div>
  <h3>OMAR VELASCO</h3><div class="role">PARTNER</div>
  <div class="socials"><i></i><i></i><i></i></div>
</article>
<article class="card active" style="left:366px">
  <div class="portrait" role="img" aria-label="Portrait of partner Rohan Delacroix"></div>
  <h3>ROHAN DELACROIX</h3><div class="role">PARTNER</div>
  <div class="socials"><i></i><i></i><i></i></div>
</article>
<article class="card" style="left:613px">
  <div class="portrait" role="img" aria-label="Portrait of partner Tariq Linwood"></div>
  <h3>TARIQ LINWOOD</h3><div class="role">PARTNER</div>
  <div class="socials"><i></i><i></i><i></i></div>
</article>
<article class="card" style="left:861px">
  <div class="portrait" role="img" aria-label="Portrait of partner Preston Hale"></div>
  <h3>PRESTON HALE</h3><div class="role">PARTNER</div>
  <div class="socials"><i></i><i></i><i></i></div>
</article>

<a class="btn" style="left:520px;top:2378px;width:160px">View More</a>

<h2 class="news-title"><b>Subscribe</b> To Our Newsletter</h2>
<p class="news-sub">To Receive The latest News And Update</p>
<div class="news-form"><span>Your E-Mail</span><div class="submit">SUBMIT</div></div>

<footer class="footer">
  <div class="brand-foot">HALVERINE</div>
  <p class="about">Lorem Ipsum is simply dummy text of the printing and typesetting industry. Lorem text of the printing and typesett Ipsum industries.</p>
  <p class="more">Read More.. <span style="display:inline-block;width:10px;height:10px;border-radius:50%;background:var(--olive)"></span></p>
  <h4 style="left:437px">QUICK LINKS</h4>
  <ul>
    <li>Venture</li><li>Private Credit</li><li>Crypto</li><li>Halverine</li><li>About us</li><li>Team</li><li>Blog</li>
  </ul>
  <h4 style="left:605px">CONTACT US</h4>
  <p class="contact">218 Marlow Street, Suite 405<br>Easton,<br>EA2040<br>+1 555 018 2247<br>info@halverine.vc</p>
  <h4 style="left:854px">QUICK CONTACT</h4>
  <div class="field" style="left:854px;top:153px;width:110px;height:20px">Name</div>
  <div class="field" style="left:968px;top:153px;width:112px;height:20px">Phone</div>
  <div class="field" style="left:854px;top:180px;width:226px;height:50px">Message</div>
  <div class="btn" style="left:963px;top:241px;width:117px;height:22px;font-size:11px">Send</div>
</footer>

<div class="bottom">
  <p>Copyright © 2018 HALVERINE.&nbsp; All Rights Reserved.</p>
  <div class="socials"><i></i><i></i><i></i><i></i><i></i></div>
</div>

</body>
</html>
```